Business Card Design

We are a commercial real estate brokerage in San Francisco, leasing office buildings downtown.
I would like a clean, elegant look. Simple but powerful .

Industry/Entity Type

Business

Contact Information for Business Card

Derek Holloway
lic# 07258143
415.555.0172
derek@velt-commercial.example
velt-commercial.example

```html
<!DOCTYPE html>
<html lang="en">
<head>
<meta charset="UTF-8">
<title>Velt Commercial – Business Card</title>
<link rel="stylesheet" href="https://fonts.googleapis.com/css2?family=Source+Sans+3:wght@400;600&display=swap">
<style>
  :root {
    --backdrop: #e6e4e0;
    --card: #ffffff;
    --band-dark: #3b3b3d;
    --slate: #7f8cab;
    --slate-deep: #6b7896;
    --ink: #4a4a4a;
    --rule: #b9bcc4;
    --illus-light: #c9c9cb;
    --illus-dark: #4e4e52;
  }
  * { box-sizing: border-box; margin: 0; padding: 0; }
  html, body { width: 1200px; height: 950px; overflow: hidden; }
  body {
    background: var(--backdrop);
    font-family: "Source Sans 3", "Helvetica Neue", Arial, sans-serif;
    position: relative;
  }
  .card {
    position: absolute;
    left: 320px;
    width: 560px;
    height: 320px;
    background: var(--card);
    overflow: hidden;
    box-shadow: 0 6px 18px rgba(0,0,0,0.18);
  }

  /* Back side */
  .card-back { top: 110px; }
  .card-back .skyline {
    position: absolute;
    left: 190px;
    top: 72px;
    width: 180px;
    height: 120px;
    background: linear-gradient(90deg, var(--illus-light), var(--illus-dark) 60%, var(--illus-light));
  }
  .card-back .tagline-band {
    position: absolute;
    left: 0; right: 0; bottom: 0;
    height: 118px;
    background: var(--band-dark);
    display: flex;
    flex-direction: column;
    justify-content: center;
    align-items: center;
    color: #f0f0f0;
    font-size: 15px;
    line-height: 1.35;
    text-align: center;
  }

  /* Front side */
  .card-front { top: 500px; }
  .brand {
    position: absolute;
    right: 40px;
    top: 56px;
    height: 36px;
    display: flex;
    align-items: center;
    gap: 12px;
    white-space: nowrap;
  }
  .brand-mark {
    flex: none;
    width: 32px; height: 32px;
    background: var(--slate);
  }
  .brand-name {
    font-size: 24px;
    line-height: 1;
    font-weight: 600;
    letter-spacing: 1px;
    color: var(--slate);
  }
  .rule-top {
    position: absolute;
    left: 250px; right: 40px; top: 112px;
    height: 1px; background: var(--rule);
  }
  .license {
    position: absolute;
    right: 40px; top: 124px;
    font-size: 14px; color: var(--ink);
  }
  .holder-name {
    position: absolute;
    left: 34px; top: 176px;
    font-size: 19px; font-weight: 600;
    line-height: 1.2;
    letter-spacing: 0.5px;
    color: var(--slate-deep);
    text-transform: uppercase;
  }
  .rule-name {
    position: absolute;
    left: 34px; right: 250px; top: 204px;
    height: 1px; background: var(--rule);
  }
  .contacts {
    position: absolute;
    left: 34px; top: 214px;
    list-style: none;
    font-size: 14px; color: var(--ink);
  }
  .contacts li { display: flex; align-items: center; gap: 10px; height: 22px; }
  .contacts svg { width: 13px; height: 13px; fill: var(--slate-deep); }
  .web-band {
    position: absolute;
    left: 0; right: 0; bottom: 0;
    height: 34px;
    background: var(--slate);
    color: #ffffff;
    font-size: 14px;
    letter-spacing: 3px;
    display: flex;
    align-items: center;
    justify-content: flex-end;
    padding-right: 40px;
    white-space: nowrap;
  }
</style>
</head>
<body>

  <section class="card card-back">
    <div class="skyline" role="img" aria-label="Illustration of downtown office towers"></div>
    <div class="tagline-band">
      <p>commercial real estate brokerage in San Francisco</p>
      <p>leasing office buildings downtown.</p>
    </div>
  </section>

  <section class="card card-front">
    <div class="brand">
      <span class="brand-mark"></span>
      <span class="brand-name">VELT COMMERCIAL</span>
    </div>
    <div class="rule-top"></div>
    <p class="license">lic# 07258143</p>

    <h1 class="holder-name">Derek Holloway</h1>
    <div class="rule-name"></div>
    <ul class="contacts">
      <li>
        <svg viewBox="0 0 24 24" aria-hidden="true"><path d="M6.6 10.8a15.1 15.1 0 0 0 6.6 6.6l2.2-2.2a1 1 0 0 1 1-.25 11.4 11.4 0 0 0 3.6.57 1 1 0 0 1 1 1V20a1 1 0 0 1-1 1A17 17 0 0 1 3 4a1 1 0 0 1 1-1h3.5a1 1 0 0 1 1 1c0 1.25.2 2.45.57 3.57a1 1 0 0 1-.25 1z"/></svg>
        415.555.0172
      </li>
      <li>
        <svg viewBox="0 0 24 24" aria-hidden="true"><path d="M2 5h20v14H2z" fill="var(--slate-deep)"/><path d="M2 5l10 8 10-8" fill="none" stroke="#fff" stroke-width="2"/></svg>
        derek@velt-commercial.example
      </li>
    </ul>

    <div class="web-band">www.velt-commercial.example</div>
  </section>

</body>
</html>
```